Business Card Design

I already have a company logo for my company. I have a logo for the manufacturer we represent. I want a professional business card design.

```html
<!DOCTYPE html>
<html lang="en">
<head>
<meta charset="utf-8">
<title>Beacon Signal LLC – Business Card</title>
<link href="https://fonts.googleapis.com/css2?family=Open+Sans:wght@400;600;800&display=swap" rel="stylesheet">
<style>
  :root{
    --bg:#e9e9ea;
    --card-white:#ffffff;
    --card-black:#1b1b1c;
    --red:#e3262c;
    --gold:#d4a21c;
    --ink:#2a2a2a;
    --muted:#555555;
    --white:#ffffff;
  }
  *{margin:0;padding:0;box-sizing:border-box}
  html,body{width:1200px;height:900px;overflow:hidden;background:var(--bg);font-family:"Open Sans",Arial,sans-serif}
  .canvas{position:relative;width:1200px;height:900px}
  .card{position:absolute;left:260px;width:680px;height:388px;border-radius:28px;overflow:hidden;box-shadow:0 6px 18px rgba(0,0,0,.18)}
  .card--front{top:45px;background:var(--card-white)}
  .card--back{top:467px;background:var(--card-black)}

  .brand-name{position:absolute;left:0;right:0;top:58px;text-align:center;font-weight:800;font-size:54px;letter-spacing:2px;color:var(--red);line-height:1}
  .brand-rule{position:absolute;left:150px;right:110px;top:128px;height:4px;background:var(--gold)}

  .person{position:absolute;left:70px;top:182px}
  .person__name{font-weight:600;font-size:26px;color:var(--red)}
  .person__role{font-size:15px;color:var(--muted);margin-top:2px}
  .divider{position:absolute;left:268px;top:178px;width:2px;height:78px;background:var(--gold)}

  .contacts{position:absolute;left:288px;top:176px;list-style:none}
  .contacts li{display:flex;align-items:center;gap:10px;font-size:15px;color:var(--ink);height:27px}
  .contacts svg{width:14px;height:14px;flex:none}

  .band-thin{position:absolute;left:0;right:0;top:298px;height:10px;background:var(--red)}
  .band-thick{position:absolute;left:0;right:0;top:318px;height:42px;background:var(--red)}
  .band-label{position:absolute;left:70px;top:327px;font-weight:800;font-size:16px;letter-spacing:1px;color:var(--white)}

  .back-mark{position:absolute;left:0;right:0;top:0;bottom:0;display:flex;align-items:center;justify-content:center;gap:16px}
  .back-mark__dot{width:26px;height:26px;border-radius:50%;background:var(--red)}
  .back-mark__name{font-weight:800;font-size:40px;letter-spacing:2px;color:var(--white)}
</style>
</head>
<body>
<main class="canvas">
  <section class="card card--front" aria-label="Card front">
    <div class="brand-name">BEACON SIGNAL LLC</div>
    <div class="brand-rule"></div>

    <div class="person">
      <div class="person__name">Dale Morgan</div>
      <div class="person__role">Managing Director</div>
    </div>
    <div class="divider"></div>

    <ul class="contacts">
      <li>
        <svg viewBox="0 0 14 14" aria-hidden="true"><path fill="#e3262c" d="M3 1h2l1 3-1.5 1a7 7 0 0 0 4.5 4.5l1-1.5 3 1v2a2 2 0 0 1-2 2A11 11 0 0 1 1 3a2 2 0 0 1 2-2z"/></svg>
        555.010.0142
      </li>
      <li>
        <svg viewBox="0 0 14 14" aria-hidden="true"><rect x="1" y="3" width="12" height="8" rx="1" fill="#e3262c"/><path d="M1.5 3.5 7 8l5.5-4.5" stroke="#fff" stroke-width="1.2" fill="none"/></svg>
        info@beaconsignalllc.com
      </li>
      <li>
        <svg viewBox="0 0 14 14" aria-hidden="true"><circle cx="7" cy="7" r="6" fill="#e3262c"/><path d="M1 7h12M7 1c2.5 3 2.5 9 0 12M7 1c-2.5 3-2.5 9 0 12" stroke="#fff" stroke-width="1" fill="none"/></svg>
        www.beaconsignalllc.com
      </li>
    </ul>

    <div class="band-thin"></div>
    <div class="band-thick"></div>
    <div class="band-label">BEACON SIGNAL LLC</div>
  </section>

  <section class="card card--back" aria-label="Card back">
    <div class="back-mark">
      <span class="back-mark__dot"></span>
      <span class="back-mark__name">BEACON SIGNAL LLC</span>
    </div>
  </section>
</main>
</body>
</html>
```